Dovecote Realty

Business cards for 4 people

They need to say for all
87 Tarrow Quay, Boston MA 02114

Each person will have their own personal information
We would like gold embossing for the name of the company
Marla is the blonde sitting in the chair smiling her information should be on the back of the card with her name and information
Should say for slogan classic pattern, elevated experience
grace@dovecoteprops.com
(413) 555-0182

Odette is the brunette with wavy hair in the tan suit odette@dovecoteprops.com
(617) 555-0137

faith@dovecoteprops.com
(413) 555-0164
standing next to the chair

hope@dovecoteprops.com
(413) 555-0199
close up headshot

```html
<!DOCTYPE html>
<html lang="en">
<head>
<meta charset="utf-8">
<title>Dovecote Realty – Business Cards</title>
<link rel="stylesheet" href="https://fonts.googleapis.com/css2?family=Cinzel:wght@400&family=Poppins:wght@300;400;600&display=swap">
<style>
  :root {
    --page-bg: #e4e4e2;
    --navy: #2e5276;
    --navy-deep: #254566;
    --gold: #c9a27c;
    --card-light: #cbcbc6;
    --card-light-2: #c6c7c1;
    --ink-logo: #4a4a48;
    --ink-body: #6e6f6b;
    --ink-name: #2c3d5e;
    --photo-wall: #d9d8d3;
    --photo-suit: #8c6a4e;
  }
  * { margin: 0; padding: 0; box-sizing: border-box; }
  html, body { width: 1200px; height: 1200px; overflow: hidden; }
  body {
    background: var(--page-bg);
    font-family: "Poppins", sans-serif;
    position: relative;
  }
  .card {
    position: absolute;
    left: 204px;
    width: 804px;
    height: 458px;
    border-radius: 20px;
    overflow: hidden;
  }
  /* Front */
  .card-front {
    top: 97px;
    background: linear-gradient(135deg, var(--navy-deep) 0%, var(--navy) 60%, #3a6386 100%);
  }
  .front-mark {
    position: absolute;
    left: 323px; top: 106px;
    width: 158px; height: 158px;
    border: 3px solid var(--gold);
    border-radius: 50%;
  }
  .front-brand {
    position: absolute;
    left: 0; right: 0; top: 275px;
    text-align: center;
    font-family: "Cinzel", serif;
    font-weight: 400;
    color: var(--gold);
  }
  .front-brand .brand-name { display: block; font-size: 50px; letter-spacing: 1px; line-height: 1; }
  .front-brand .brand-sub { display: block; font-size: 20px; letter-spacing: 14px; margin-top: 10px; padding-left: 14px; }

  /* Back */
  .card-back {
    top: 627px;
    background: linear-gradient(90deg, var(--card-light) 0%, var(--card-light-2) 100%);
  }
  .back-photo {
    position: absolute;
    right: 0; top: 0;
    width: 500px; height: 100%;
    background:
      radial-gradient(ellipse 120px 230px at 60% 65%, var(--photo-suit) 0%, rgba(140,106,78,0.6) 55%, rgba(140,106,78,0) 100%),
      linear-gradient(90deg, rgba(217,216,211,0) 0%, var(--photo-wall) 35%, #e2e1dc 100%);
  }
  .back-brand {
    position: absolute;
    left: 54px; top: 56px;
    width: 212px;
    text-align: center;
    font-family: "Cinzel", serif;
    font-weight: 400;
    color: var(--ink-logo);
  }
  .back-mark {
    width: 74px; height: 74px;
    margin: 0 auto 8px;
    border: 2px solid var(--ink-logo);
    border-radius: 50%;
  }
  .back-brand .brand-name { display: block; font-size: 25px; line-height: 1; }
  .back-brand .brand-sub { display: block; font-size: 11px; letter-spacing: 7px; padding-left: 7px; margin-top: 4px; }
  .address {
    position: absolute; left: 54px; top: 186px;
    font-size: 13px; font-weight: 300; color: var(--ink-body);
  }
  .person-name {
    position: absolute; left: 54px; top: 262px;
    font-size: 24px; font-weight: 600; color: var(--ink-name);
  }
  .contact {
    position: absolute; left: 54px;
    display: flex; align-items: center; gap: 10px;
    font-size: 14px; font-weight: 300; color: var(--ink-body);
  }
  .contact-email { top: 304px; }
  .contact-phone { top: 331px; }
  .contact svg { fill: var(--ink-body); }
  .website {
    position: absolute; left: 54px; top: 390px;
    font-size: 14px; font-weight: 300; color: var(--ink-body);
  }
  .website strong { font-weight: 600; }
</style>
</head>
<body>
  <section class="card card-front">
    <div class="front-mark"></div>
    <div class="front-brand">
      <span class="brand-name">DOVECOTE</span>
      <span class="brand-sub">REALTY</span>
    </div>
  </section>

  <section class="card card-back">
    <div class="back-photo" role="img" aria-label="Portrait photo of Odette, seated on a wooden chair in a tan suit against a pale wall"></div>
    <div class="back-brand">
      <div class="back-mark"></div>
      <span class="brand-name">DOVECOTE</span>
      <span class="brand-sub">REALTY</span>
    </div>
    <p class="address">87 Tarrow Quay, Boston MA 02114</p>
    <h1 class="person-name">Odette Marchand</h1>
    <p class="contact contact-email">
      <svg width="13" height="10" viewBox="0 0 13 10" aria-hidden="true"><path d="M0 0h13v10H0z M1 1.2v0.4l5.5 3.8 5.5-3.8v-0.4z" fill-rule="evenodd"/></svg>
      odette@dovecoteprops.com
    </p>
    <p class="contact contact-phone">
      <svg width="13" height="18" viewBox="0 0 13 18" aria-hidden="true"><path d="M2 0h9a2 2 0 0 1 2 2v14a2 2 0 0 1-2 2H2a2 2 0 0 1-2-2V2a2 2 0 0 1 2-2zm0 2v12h9V2zm4.5 13a1 1 0 1 0 0 2 1 1 0 0 0 0-2z" fill-rule="evenodd"/></svg>
      (617) 555-0137
    </p>
    <p class="website"><strong>dovecoteprops</strong>.com</p>
  </section>
</body>
</html>
```